New Business Card Design

We need a business card design for a new company based in Sydney called "Haven and Hue". This is an online buisness which will have an online store providing imported homewares.
We are looking for something that is different, perhaps even in shape and using the logo that was designed by Pixel Harbor.

Attached document is a basic example I want to see more creative versions.

Target Market(s)

Homewares, Interior Design

Industry/Entity Type

Business

Contact Information for Business Card

Company Logo
Company Name
Industry area
Name
Position
Phone
Email
Website
Motto

Requirements
Must have
• Logo
Nice to have
• Social website logos - Chatterloop, Glimmoraly, Quibbly, Boardlyne, Veltrix+

```html
<!DOCTYPE html>
<html lang="en">
<head>
<meta charset="utf-8">
<title>Haven and Hue — Business Card</title>
<link rel="stylesheet" href="https://fonts.googleapis.com/css2?family=Lato:wght@400;700&display=swap">
<style>
  :root {
    --page-bg: #e7e1d8;
    --frost-top: #f4f3f1;
    --frost-bottom: #d9dbdd;
    --panel-black: #151515;
    --panel-edge: #2c2c2c;
    --gold: #b8895a;
    --gold-light: #e2c39a;
    --copper: #c88b5e;
    --rose: #d7a6a0;
    --contact: #c9b99c;
    --charcoal: #262626;
  }
  * { box-sizing: border-box; margin: 0; padding: 0; }
  html, body {
    width: 1200px; height: 970px; overflow: hidden;
    background: var(--page-bg);
    font-family: "Lato", sans-serif;
  }
  .card {
    position: absolute; left: 150px; top: 232px;
    width: 900px; height: 506px;
    border-radius: 16px; overflow: hidden;
    background: linear-gradient(180deg, var(--frost-top), var(--frost-bottom));
    box-shadow: 0 10px 30px rgba(0,0,0,.18);
  }
  .card-shapes { position: absolute; inset: 0; }
  .brand {
    position: absolute; left: 60px; top: 118px;
    display: flex; align-items: center; gap: 14px;
  }
  .brand-dot { width: 20px; height: 20px; border-radius: 50%; background: var(--charcoal); }
  .brand-name { font-size: 40px; font-weight: 700; color: var(--charcoal); letter-spacing: .5px; }
  .social {
    position: absolute; right: 40px; top: 42px;
    display: flex; gap: 12px; list-style: none;
  }
  .social li {
    display: flex; align-items: center; gap: 5px;
    font-size: 12px; font-weight: 700; color: var(--charcoal);
  }
  .social li::before {
    content: ""; width: 14px; height: 14px; border-radius: 50%;
    background: var(--charcoal);
  }
  .person {
    position: absolute; left: 0; width: 462px; top: 372px; text-align: center;
  }
  .person-name { font-size: 32px; color: var(--copper); line-height: 1; }
  .person-role { font-size: 24px; color: var(--rose); margin-top: 10px; line-height: 1; }
  .divider {
    position: absolute; left: 439px; top: 330px; width: 2px; height: 176px;
    background: linear-gradient(180deg, transparent, var(--gold) 30%, var(--gold) 70%, transparent);
  }
  .address {
    position: absolute; left: 507px; top: 326px;
    font-size: 22px; line-height: 30px; color: var(--contact); font-style: normal;
  }
  .contacts {
    position: absolute; left: 503px; top: 402px; list-style: none;
    font-size: 22px; line-height: 30px; color: var(--contact);
  }
  .contacts li { display: flex; align-items: center; gap: 14px; }
  .contacts .phone-number { font-size: 24px; letter-spacing: 2px; }
  .contacts svg { width: 22px; height: 22px; flex: none; }
</style>
</head>
<body>
  <article class="card">
    <svg class="card-shapes" viewBox="0 0 900 506" width="900" height="506" aria-hidden="true">
      <defs>
        <linearGradient id="gold-band" x1="0" y1="0" x2="1" y2="0">
          <stop offset="0" stop-color="#9c6b3e"/>
          <stop offset=".35" stop-color="#e2c39a"/>
          <stop offset=".7" stop-color="#b8895a"/>
          <stop offset="1" stop-color="#b8895a" stop-opacity="0"/>
        </linearGradient>
        <linearGradient id="black-panel" x1="0" y1="0" x2="0" y2="1">
          <stop offset="0" stop-color="#2a2a2a"/>
          <stop offset=".3" stop-color="#151515"/>
          <stop offset="1" stop-color="#0d0d0d"/>
        </linearGradient>
      </defs>
      <path class="gold-swoosh" d="M0,232 C160,300 330,300 480,258 C600,226 700,208 790,208 C700,214 600,236 490,272 C340,320 170,320 0,276 Z" fill="url(#gold-band)"/>
      <path class="black-wave" d="M0,292 C190,338 380,305 540,250 C680,205 810,204 900,226 L900,506 L0,506 Z" fill="url(#black-panel)"/>
    </svg>

    <div class="brand">
      <span class="brand-dot"></span>
      <span class="brand-name">Haven and Hue</span>
    </div>

    <ul class="social">
      <li>Chatterloop</li>
      <li>Quibbly</li>
      <li>Glimmoraly</li>
      <li>Boardlyne</li>
      <li>Veltrix+</li>
    </ul>

    <div class="person">
      <p class="person-name">Marcus Elland</p>
      <p class="person-role">Director</p>
    </div>

    <div class="divider"></div>

    <address class="address">
      Unit 4, Linden Avenue<br>
      Harbourside 2000 NSW AU
    </address>

    <ul class="contacts">
      <li>
        <svg viewBox="0 0 22 22" aria-hidden="true"><rect x="6" y="2" width="10" height="18" rx="2" fill="none" stroke="#c9b99c" stroke-width="1.6"/><line x1="9.5" y1="17" x2="12.5" y2="17" stroke="#c9b99c" stroke-width="1.4"/></svg>
        <span class="phone-number">0298765432</span>
      </li>
      <li>
        <svg viewBox="0 0 22 22" aria-hidden="true"><rect x="2" y="5" width="18" height="13" fill="#c9b99c"/><path d="M2,5 L11,12 L20,5" fill="none" stroke="#151515" stroke-width="1.4"/></svg>
        <span>me@havenandhue.com.au</span>
      </li>
      <li>
        <svg viewBox="0 0 22 22" aria-hidden="true"><circle cx="11" cy="11" r="8.5" fill="none" stroke="#c9b99c" stroke-width="1.6"/><ellipse cx="11" cy="11" rx="3.5" ry="8.5" fill="none" stroke="#c9b99c" stroke-width="1.2"/><line x1="2.5" y1="11" x2="19.5" y2="11" stroke="#c9b99c" stroke-width="1.2"/></svg>
        <span>www.havenandhue.com.au</span>
      </li>
    </ul>
  </article>
</body>
</html>
```